Business Cards - Brightpath Horizon

need to design unique business card for my mortgage business. I need to design credit card style business card for my business or any unique idea that you might have

Target Market(s)

Home Loan customers

Industry/Entity Type

Mortgage Brokerage

Contact Information for Business Card

please design credit card style or very unique style business card

Colors

Designer to choose colors to be used in the design.

Requirements
Must have
• Name
• position
• Phone number
• fax number
• email address
• website address
• social media address
• All above fields will be provided once design in finalised

```html
<!DOCTYPE html>
<html lang="en">
<head>
<meta charset="utf-8">
<title>Brightpath Horizon – Business Card</title>
<link rel="stylesheet" href="https://fonts.googleapis.com/css2?family=Libre+Baskerville:wght@700&family=Open+Sans:wght@400;600&display=swap">
<style>
  :root {
    --page: #eceae7;
    --card: #ffffff;
    --royal: #0a2fc4;
    --royal-dark: #1b2f9e;
    --amber: #f7901e;
    --white: #ffffff;
  }
  * { margin: 0; padding: 0; box-sizing: border-box; }
  html, body {
    width: 1200px; height: 900px; overflow: hidden;
    background: var(--page);
  }
  .card {
    position: absolute; left: 100px; top: 141px;
    width: 1000px; height: 618px;
    background: var(--card);
    overflow: hidden;
    box-shadow: 0 18px 40px rgba(0,0,0,0.18);
  }
  .wave { position: absolute; inset: 0; width: 100%; height: 100%; }
  .brand {
    position: absolute; left: 96px; top: 150px;
    display: flex; align-items: center; gap: 18px;
  }
  .brand-mark { width: 24px; height: 24px; background: var(--royal-dark); flex: none; }
  .brand-name {
    font-family: "Open Sans", Arial, sans-serif;
    font-weight: 600; color: var(--royal-dark);
    font-size: 44px; line-height: 1.12;
  }
  .tagline {
    position: absolute; left: 138px; top: 290px;
    font-family: "Open Sans", Arial, sans-serif;
    font-weight: 400; color: var(--amber); font-size: 22px;
  }
  .person {
    position: absolute; right: 50px; top: 72px; text-align: right;
  }
  .person-name {
    font-family: "Libre Baskerville", Georgia, serif;
    font-weight: 700; color: var(--royal-dark);
    font-size: 30px; letter-spacing: 0.5px;
  }
  .person-role {
    font-family: "Open Sans", Arial, sans-serif;
    color: var(--amber); font-size: 24px; margin-top: 2px;
  }
  .social {
    position: absolute; right: 48px; top: 350px;
    display: flex; gap: 12px; list-style: none;
  }
  .social li { width: 43px; height: 43px; background: var(--white); }
  .contacts {
    position: absolute; right: 48px; top: 432px;
    list-style: none; text-align: right;
    font-family: "Open Sans", Arial, sans-serif;
    color: var(--white); font-size: 26px; line-height: 37px;
  }
  .contacts li { display: flex; justify-content: flex-end; align-items: center; gap: 10px; }
  .contacts svg { width: 20px; height: 20px; fill: var(--white); flex: none; }
</style>
</head>
<body>
  <div class="card">
    <svg class="wave" viewBox="0 0 652 403" preserveAspectRatio="none" aria-hidden="true">
      <path d="M0,222 C80,300 170,340 285,305 C400,268 490,130 590,130 C620,132 640,150 652,172 L652,403 L0,403 Z" fill="var(--royal)"/>
      <path d="M0,208 C80,288 170,326 282,291 C400,253 485,110 590,112 C622,114 642,134 652,152" fill="none" stroke="var(--amber)" stroke-width="9"/>
    </svg>

    <div class="brand">
      <span class="brand-mark"></span>
      <div class="brand-name">Brightpath<br>Horizon</div>
    </div>
    <p class="tagline">Your home, our priority</p>

    <div class="person">
      <h1 class="person-name">DANIEL WHITFORD</h1>
      <p class="person-role">Managing Director</p>
    </div>

    <ul class="social" aria-label="Social media">
      <li></li><li></li><li></li>
    </ul>

    <ul class="contacts">
      <li>(044)555019283
        <svg viewBox="0 0 20 20" aria-label="Phone"><path d="M2,7 C2,4 6,3 10,3 C14,3 18,4 18,7 L14,8 L13,6 C11,5.5 9,5.5 7,6 L6,8 Z M5,9 L15,9 L17,16 L3,16 Z"/></svg>
      </li>
      <li>(044)555019283
        <svg viewBox="0 0 20 20" aria-label="Fax"><path d="M5,2 H12 L15,5 V8 H5 Z M3,9 H17 V18 H3 Z" /><rect x="6" y="11" width="8" height="1.6" fill="var(--royal)"/><rect x="6" y="14" width="8" height="1.6" fill="var(--royal)"/></svg>
      </li>
      <li>info@brightpathhorizon.com
        <svg viewBox="0 0 20 20" aria-label="Email"><path d="M2,5 H18 V16 H2 Z"/><path d="M2,5 L10,11 L18,5" fill="none" stroke="var(--royal)" stroke-width="1.5"/></svg>
      </li>
      <li>www.brightpathhorizon.com
        <svg viewBox="0 0 20 20" aria-label="Website"><circle cx="10" cy="10" r="8"/><path d="M4,8 C7,6 9,9 8,12 C7,14 9,16 10,17 M13,4 C12,7 15,8 17,9" fill="none" stroke="var(--royal)" stroke-width="1.4"/></svg>
      </li>
    </ul>
  </div>
</body>
</html>
```